New Business Cards for NYC Salon

We are updating all of our cards. 7142-8863-2095 is my account number. We put names of our stylists on their cards. The back should include appointment space. Were looking for something more sleek and modern. Black/White Silver... or even touches of the orange color on our website which has been our thing for years. The design should communicate professional upscale boutique salon for men and women. Should be able to incorporate design into thank you cards, referral cards, brochure and postcards. The file is a zip file...we like the stacked ones black or white or the side versions.

Industry/Entity Type

Beauty Salon

Contact Information for Business Card

Marcus John's Salon313 W. 53rd Street, New York NY 10019 212-683-2741 info@marcusellingsalon.example www.marcusellingsalon.example

Font styles to use
Other font styles liked:
• trajan

Requirements
Must have
• we print a different card for every person in the salon. Begin by designing with the name Marcus. We will change it with every employee when printing. Must have a space for appointment date and time.
Nice to have
• Were looking to move towards the stacked or side placed logo but not opposed to utilizing the circular.
Should not have
• Photos

```html
<!DOCTYPE html>
<html lang="en">
<head>
<meta charset="utf-8">
<title>Marcus Elling's Salon – Business Card</title>
<link rel="stylesheet" href="https://fonts.googleapis.com/css2?family=Open+Sans:wght@400;700&display=swap">
<style>
  :root {
    --backdrop: #3a322e;
    --card: #0d0d0d;
    --card-edge: #1c1c1c;
    --ink: #ffffff;
    --ink-soft: #d9d9d9;
    --rule: #6a6a6a;
  }
  * { box-sizing: border-box; margin: 0; padding: 0; }
  html, body { width: 1200px; height: 844px; overflow: hidden; }
  body {
    background: var(--backdrop);
    font-family: "Open Sans", Arial, sans-serif;
    color: var(--ink);
    position: relative;
  }
  .card {
    position: absolute;
    width: 500px;
    height: 286px;
    background: linear-gradient(160deg, #1a1a1a 0%, var(--card) 55%);
    border: 1px solid var(--card-edge);
    box-shadow: 0 10px 30px rgba(0,0,0,.45);
  }
  .card--front { left: 70px; top: 279px; }
  .card--back  { left: 630px; top: 279px; }

  /* Front */
  .brand {
    position: absolute; left: 0; top: 0; width: 200px; height: 100%;
    display: flex; align-items: center; justify-content: center;
  }
  .brand__name {
    font-size: 15px; font-weight: 400; text-align: center;
    line-height: 1.4; color: var(--ink);
  }
  .divider {
    position: absolute; left: 200px; top: 40px; width: 1px; height: 206px; background: var(--rule);
  }
  .details { position: absolute; left: 228px; top: 52px; right: 20px; }
  .details__title { font-size: 20px; font-weight: 700; margin-bottom: 14px; }
  .details__address { font-size: 13px; line-height: 1.4; color: var(--ink-soft); margin-bottom: 14px; }
  .details__contact { font-size: 13px; line-height: 1.55; color: var(--ink-soft); list-style: none; }

  /* Back */
  .appt { position: absolute; inset: 30px 34px; }
  .appt__title { font-size: 18px; font-weight: 700; text-align: center; margin-bottom: 20px; }
  .field { display: flex; align-items: flex-end; font-size: 12px; color: var(--ink-soft); margin-bottom: 16px; gap: 8px; }
  .field__line { flex: 1; border-bottom: 1px solid var(--rule); height: 14px; }
  .days { display: flex; justify-content: space-between; font-size: 11px; color: var(--ink-soft); margin-bottom: 18px; }
  .day { display: flex; align-items: center; gap: 3px; }
  .day__box { width: 11px; height: 11px; border: 1px solid var(--ink); }
</style>
</head>
<body>
  <section class="card card--front" aria-label="Business card front">
    <div class="brand">
      <p class="brand__name">Marcus Elling's Salon</p>
    </div>
    <span class="divider"></span>
    <div class="details">
      <h1 class="details__title">Marcus Elling's Salon</h1>
      <p class="details__address">742 E. 18th Street,<br>New York NY 10003</p>
      <ul class="details__contact">
        <li>T: 212-683-2741</li>
        <li>E: info@marcusellingsalon.example</li>
        <li>W: www.marcusellingsalon.example</li>
      </ul>
    </div>
  </section>

  <section class="card card--back" aria-label="Business card back">
    <div class="appt">
      <h2 class="appt__title">Your Next Appointment is</h2>
      <div class="field"><span>Name :</span><span class="field__line"></span></div>
      <div class="field"><span>Date :</span><span class="field__line"></span></div>
      <div class="days">
        <span class="day">MON<span class="day__box"></span></span>
        <span class="day">TUE<span class="day__box"></span></span>
        <span class="day">WED<span class="day__box"></span></span>
        <span class="day">THU<span class="day__box"></span></span>
        <span class="day">FRI<span class="day__box"></span></span>
        <span class="day">SAT<span class="day__box"></span></span>
        <span class="day">SUN<span class="day__box"></span></span>
      </div>
      <div class="field">
        <span>Time:</span><span class="field__line"></span><span>AM</span><span class="field__line"></span><span>PM</span>
      </div>
    </div>
  </section>
</body>
</html>
```